Veranix - Solution provider in business consulting

Veranix is a swiss based company providing solutions for developing markets. The business covers various fields of business consulting, such as supply chain, product costs, quality management and manufacturing management. The Business operates in a efficient, straight and solution oriented manner.
The final design should communicate these characteristics. Asian people as well as as western people shall identify the qualities of the company at first sight.
The customer needs business cards with a simple view but an recognizable design, printed in high quality. Engraved elements such as the globe or simple words are possible.
Available colors are: (RAL)
102/102/102
51/102/102
153/204/153
255/102/51
Font: Calibri

```html
<!DOCTYPE html>
<html lang="en">
<head>
<meta charset="utf-8">
<title>Veranix business card</title>
<link rel="stylesheet" href="https://fonts.googleapis.com/css2?family=Carlito:wght@400;700&display=swap">
<style>
  :root {
    --brand-grey: #666666;
    --paper: #ffffff;
    --backdrop: #e8e8e6;
    --ink-light: #ffffff;
  }
  * { margin: 0; padding: 0; box-sizing: border-box; }
  html, body { width: 1200px; height: 900px; overflow: hidden; }
  body {
    background: var(--backdrop);
    font-family: "Carlito", Calibri, sans-serif;
    position: relative;
  }
  .card {
    position: absolute;
    overflow: hidden;
    box-shadow: 0 2px 8px rgba(0,0,0,0.15);
  }
  .card-front {
    left: 78px; top: 35px; width: 588px; height: 362px;
    background: var(--paper);
  }
  .card-back {
    left: 388px; top: 505px; width: 567px; height: 352px;
    background: var(--brand-grey);
  }
  .front-band { position: absolute; left: 0; top: 0; width: 588px; height: 362px; }
  .wordmark {
    position: absolute;
    display: flex; align-items: center; gap: 14px;
    font-weight: 400;
    letter-spacing: 1px;
    line-height: 1;
  }
  .wordmark-dot { border-radius: 50%; flex: none; }
  .card-front .wordmark {
    left: 0; width: 588px; justify-content: center; top: 64px;
    font-size: 70px; color: var(--brand-grey);
  }
  .card-front .wordmark-dot { width: 26px; height: 26px; background: var(--brand-grey); }
  .card-back .wordmark {
    left: 0; width: 567px; justify-content: center; top: 138px;
    font-size: 68px; color: var(--ink-light);
  }
  .card-back .wordmark-dot { width: 26px; height: 26px; background: var(--ink-light); }
  .contact-list {
    position: absolute; right: 314px; top: 232px;
    list-style: none; color: var(--ink-light);
    font-size: 16px; text-align: right;
  }
  .contact-list li {
    display: flex; justify-content: flex-end; align-items: center;
    gap: 9px; height: 24px;
  }
  .contact-list svg { width: 12px; height: 12px; flex: none; }
  .person {
    position: absolute; left: 297px; top: 225px; color: var(--ink-light);
  }
  .person-name { font-size: 21px; font-weight: 700; line-height: 1.2; }
  .person-role { font-size: 15px; line-height: 1.2; margin-bottom: 22px; }
  .company-address { font-size: 16px; line-height: 1.3; font-style: normal; }
</style>
</head>
<body>

<section class="card card-front" aria-label="Business card front">
  <svg class="front-band" viewBox="0 0 588 362" aria-hidden="true">
    <rect x="0" y="177" width="588" height="185" fill="#666666"/>
    <polyline points="0,210 384,210 414,178 588,178" fill="none" stroke="#ffffff" stroke-width="2.5"/>
  </svg>

  <div class="wordmark"><span>veranix</span><span class="wordmark-dot"></span></div>

  <ul class="contact-list">
    <li>+41 79 300 1845
      <svg viewBox="0 0 12 12"><rect x="3" y="0.5" width="6" height="11" rx="1" fill="none" stroke="#fff" stroke-width="1.2"/><circle cx="6" cy="9.5" r="0.7" fill="#fff"/></svg>
    </li>
    <li>+41 71 900 3318
      <svg viewBox="0 0 12 12"><path d="M2.5 1 L4.5 1 L5.3 3.6 L4 4.6 C4.7 6.2 5.8 7.3 7.4 8 L8.4 6.7 L11 7.5 L11 9.5 C11 10.3 10.3 11 9.5 11 C5 11 1 7 1 2.5 C1 1.7 1.7 1 2.5 1 Z" fill="#fff"/></svg>
    </li>
    <li>marco.lind@veranix.ch
      <svg viewBox="0 0 12 12"><rect x="0.5" y="2" width="11" height="8" fill="#fff"/><polyline points="0.5,2 6,6.5 11.5,2" fill="none" stroke="#666" stroke-width="1"/></svg>
    </li>
    <li>www.veranix.ch
      <svg viewBox="0 0 12 12"><circle cx="6" cy="6" r="5.5" fill="#fff"/><path d="M0.5 6 H11.5 M6 0.5 C3.5 3 3.5 9 6 11.5 M6 0.5 C8.5 3 8.5 9 6 11.5" fill="none" stroke="#666" stroke-width="0.8"/></svg>
    </li>
  </ul>

  <div class="person">
    <p class="person-name">Marco Lind</p>
    <p class="person-role">CEO</p>
    <address class="company-address">Veranix GmbH Talweg 14<br>8472 Seebach Switzerland</address>
  </div>
</section>

<section class="card card-back" aria-label="Business card back">
  <div class="wordmark"><span>veranix</span><span class="wordmark-dot"></span></div>
</section>

</body>
</html>
```